redesign my website bluekeelvoyages.net and make it user friendly

I already have a website, bluekeelvoyages.net, and want a redesign in WordPress with Elementor Pro, using the same text/content. The goal is to improve:

Design quality (colors, fonts, spacing, visual flow)
User experience (easy navigation, clear offers)
Conversion readiness (calls-to-action, trust signals, booking flow)
Technical side (SEO basics, fast speed, full mobile responsiveness)

The site should look modern, clean, fun, engaging, interactive and optimized for speed and usability.

I would like the 11 page to be consolidate dto 6 as follows: Home (main landing, highlights)

Sailboat Trips (all packages, itineraries, pricing)
Boats (fleet details, features, photos)
How It Works (booking process, FAQs, travel info, what to expect)
Blog
Contact Us (form, ChatLine, phone, etc.)

Target Market(s)

sailboat trip customers for San Blas Islands in Panama

Industry/Entity Type

Travel, Boat Tour Agency

Coding

Coded - Design and coding required

Number of Pages Required

3 page

Font styles to use
Sans Serif
Other font styles liked:
• Oswalg and sans serif

Colors
0054AA
0677BA
7BADD7
CADEEF
E8F1F8
0094D4
00A9DD
6FCCEA
C7EBF8
E9F6FB
FFC000
F8CF3A
FAE287
FDF2CF
FEFAEE
F0912C
F2A743
F7CA91
FBE8D2
FDF5EE

Requirements
Must have
• Home (main landing, highlights) Sailboat Trips (all packages, itineraries, pricing) Boats (fleet details, features, photos) How It Works (booking process, FAQs, travel info, what to expect) Blog (updates, travel tips, inspiration) Contact Us (form, ChatLine, phone, etc.)
Nice to have
• I want it to look professionla and be very user friendy to entice people to contact me to book boat trips
Should not have
• a store

```html
<!DOCTYPE html>
<html lang="en">
<head>
<meta charset="utf-8">
<title>Blue Keel Voyages – San Blas Islands Sailing</title>
<link href="https://fonts.googleapis.com/css2?family=Oswald:wght@400;500;600&family=Poppins:wght@400;500;600&display=swap" rel="stylesheet">
<style>
:root{
  --navy:#0a2a5c;
  --navy-deep:#071f47;
  --blue:#0054AA;
  --blue-mid:#0677BA;
  --cyan:#00A9DD;
  --sky:#6FCCEA;
  --sky-pale:#C7EBF8;
  --sky-wash:#E9F6FB;
  --gold:#FFC000;
  --orange:#F0912C;
  --orange-soft:#F2A743;
  --cream:#FDF5EE;
  --text:#4b5563;
  --white:#fff;
}
*{box-sizing:border-box;margin:0;padding:0}
html,body{width:1200px;height:4528px;overflow:hidden}
body{position:relative;background:var(--white);font-family:'Poppins',sans-serif;color:var(--text)}
.abs{position:absolute}
.display{font-family:'Oswald',sans-serif;text-transform:uppercase;color:var(--navy);font-weight:500;letter-spacing:.3px}
.btn{position:absolute;display:flex;align-items:center;justify-content:center;border-radius:40px;background:linear-gradient(90deg,var(--gold),var(--orange-soft));color:var(--white);font-family:'Oswald',sans-serif;text-transform:uppercase;font-weight:500;letter-spacing:.4px;box-shadow:0 8px 18px rgba(240,145,44,.28)}
.photo{position:absolute}

/* header */
.site-header{position:absolute;left:0;top:0;width:1200px;height:92px;background:var(--white);display:flex;align-items:center;padding:0 84px;z-index:5}
.brand{display:flex;align-items:center;gap:10px;font-family:'Oswald',sans-serif;font-weight:600;font-size:22px;color:var(--navy);text-transform:uppercase}
.brand-dot{width:28px;height:28px;border-radius:50%;background:var(--cyan)}
.main-nav{display:flex;gap:22px;margin-left:72px;font-family:'Oswald',sans-serif;font-size:11.5px;text-transform:uppercase;color:var(--navy)}
.main-nav .active{color:var(--orange)}
.lang{margin-left:28px;font-family:'Oswald',sans-serif;font-size:11px;color:var(--navy)}
.site-header .btn{position:relative;margin-left:28px;width:106px;height:38px;font-size:12px}

/* hero */
.hero-photo{left:0;top:92px;width:1200px;height:830px;background:linear-gradient(180deg,#3f8fb8 0%,#3b7a4a 24%,#1e88b8 52%,#0d79b5 100%)}
.hero-title{left:84px;top:252px;font-size:66px;line-height:66px;color:var(--white);font-weight:500;width:560px}
.hero-sub{left:84px;top:470px;font-family:'Oswald',sans-serif;font-size:22px;color:var(--white);text-transform:uppercase}
.hero .btn{left:84px;top:521px;width:248px;height:55px;font-size:17px}

/* about */
.about-photo{left:111px;top:831px;width:474px;height:474px;border-radius:50%;background:radial-gradient(circle at 40% 40%,#e7d3a9 0%,#5fb9b5 45%,#148a9e 100%);box-shadow:0 20px 40px rgba(0,0,0,.18)}
.eyebrow{display:flex;align-items:center;gap:8px;font-family:'Oswald',sans-serif;font-size:14px;color:var(--navy);text-transform:uppercase}
.eyebrow::before{content:"";width:36px;height:4px;border-radius:2px;background:var(--orange)}
.about-eyebrow{left:643px;top:951px}
.about-title{left:643px;top:980px;font-size:36px}
.about-text{left:643px;top:1040px;width:405px;font-size:13.4px;line-height:21.2px}
.about .btn{left:643px;top:1188px;width:158px;height:54px;font-size:17px}

/* tours */
.tours-title{left:0;top:1378px;width:1200px;text-align:center;font-size:36px;line-height:41px}
.tour-card{position:absolute;top:1573px;width:318px;height:242px;border-radius:14px;padding:68px 30px 0 34px}
.tour-card h3{font-family:'Oswald',sans-serif;font-weight:500;font-size:17px;color:var(--navy);text-transform:uppercase;margin-bottom:14px}
.tour-card p{font-size:12.4px;line-height:18.6px}
.tour-icon{position:absolute;top:-48px;left:34px;width:88px;height:88px;border-radius:50%;display:flex;align-items:center;justify-content:center}
.tour-private{left:109px;background:var(--sky-wash);border:1.5px solid var(--sky-pale)}
.tour-private .tour-icon{background:linear-gradient(135deg,var(--sky),var(--cyan))}
.tour-shared{left:441px;background:var(--cream);border:1.5px solid #f7ca91}
.tour-shared .tour-icon{background:linear-gradient(135deg,var(--gold),var(--orange))}
.tour-family{left:773px;background:#E8F1F8;border:1.5px solid var(--blue-mid)}
.tour-family .tour-icon{background:linear-gradient(135deg,var(--blue),var(--navy))}
.tours .btn{left:500px;top:1841px;width:200px;height:55px;font-size:18px}

/* fleet */
.fleet-bg{left:0;top:1930px;width:1200px;height:730px}
.fleet-title{left:0;top:2082px;width:1200px;text-align:center;font-size:38px;color:var(--white)}
.fleet-sub{left:0;top:2136px;width:1200px;text-align:center;font-family:'Oswald',sans-serif;font-size:15px;color:var(--white);text-transform:uppercase}
.boat-card{position:absolute;top:2194px;width:306px;height:456px;background:var(--white);border-radius:18px;padding:5px;box-shadow:0 12px 30px rgba(0,40,90,.15)}
.boat-photo{height:212px;border-radius:14px}
.boat-body{padding:20px 22px}
.tag{display:inline-block;padding:4px 16px;border-radius:20px;background:var(--sky-wash);color:var(--sky);font-family:'Oswald',sans-serif;font-size:9px;text-transform:uppercase}
.boat-body h3{font-family:'Oswald',sans-serif;font-weight:500;font-size:23px;color:var(--navy);text-transform:uppercase;margin:14px 0 6px}
.boat-body .desc{font-size:12.6px}
.specs{display:flex;gap:24px;margin-top:18px;font-family:'Oswald',sans-serif;font-size:8.5px;color:var(--navy);text-transform:uppercase;line-height:10px}
.spec{display:flex;align-items:center;gap:6px}
.spec svg{width:14px;height:14px}
.boat-card .btn{position:relative;margin-top:22px;width:104px;height:34px;font-size:11px;box-shadow:none}

/* testimonial */
.quote-mark{left:36px;top:2820px;font-family:'Oswald',sans-serif;font-size:230px;line-height:1;color:var(--sky-pale)}
.testi-eyebrow{left:124px;top:2876px}
.testi-title{left:124px;top:2904px;font-size:36px}
.testi-text{left:124px;top:2962px;width:420px;font-size:13.3px;line-height:21.3px}
.arrow{position:absolute;top:3220px;width:44px;height:44px;border-radius:50%;display:flex;align-items:center;justify-content:center;color:var(--white);font-size:18px}
.arrow-prev{left:124px;background:linear-gradient(135deg,var(--sky),var(--cyan))}
.arrow-next{left:178px;background:linear-gradient(135deg,var(--gold),var(--orange))}
.testi-photo{left:661px;top:2758px;width:600px;height:600px;border-radius:50%;background:radial-gradient(circle at 50% 30%,#dfe7ee 0%,#7aa3c2 40%,#2f5f86 100%)}

/* inquiry */
.inquiry-photo{left:0;top:3340px;width:1200px;height:760px;background:linear-gradient(180deg,#ffffff 0%,#e8f3f8 18%,#7fb27f 30%,#d9e6ec 52%,#4fc3d6 72%,#1a94b4 100%)}
.inquiry-title{left:618px;top:3462px;font-size:38px}
.form{position:absolute;left:618px;top:3528px;width:453px}
.row{display:flex;gap:8px;margin-bottom:8px}
.field{flex:1;height:38px;border-radius:20px;background:var(--white);border:1.5px solid #c9d7e6;display:flex;align-items:center;padding-left:22px;font-family:'Oswald',sans-serif;font-size:9px;text-transform:uppercase;color:var(--navy)}
.radio-row{display:flex;gap:62px;padding-left:24px;margin:2px 0 10px;font-family:'Oswald',sans-serif;font-size:9px;color:var(--navy);text-transform:uppercase}
.radio-row span::before{content:"";display:inline-block;width:11px;height:11px;border-radius:50%;border:1px solid #9aa9bb;background:#fff;vertical-align:-2px;margin-right:6px}
.label{font-family:'Oswald',sans-serif;font-size:9px;color:var(--navy);text-transform:uppercase;padding-left:24px;margin:6px 0 6px}
.area{height:126px;border-radius:22px;background:var(--white);border:1.5px solid #c9d7e6;margin-top:8px}
.inquiry .btn{left:618px;top:3862px;width:180px;height:54px;font-size:17px}

/* footer */
.site-footer{position:absolute;left:0;top:4096px;width:1200px;height:432px;background:var(--navy-deep);color:var(--white)}
.foot-mark{left:90px;top:56px;width:160px;height:160px;display:flex;align-items:center;justify-content:center;font-family:'Oswald',sans-serif;font-size:22px;font-weight:500;text-transform:uppercase;color:var(--white);text-align:center;line-height:26px}
.foot-about{left:276px;top:110px;width:300px;font-size:10.5px;line-height:18px;color:#dbe6f5}
.foot-h{font-family:'Oswald',sans-serif;font-size:17px;font-weight:500;text-transform:uppercase}
.explore{left:672px;top:52px}
.explore ul{list-style:none;margin-top:14px;font-size:10.5px;line-height:20.6px}
.touch{left:852px;top:52px}
.contact-item{display:flex;gap:12px;align-items:center;margin-top:18px;font-size:10.5px;line-height:15px}
.contact-item i{width:30px;height:30px;border-radius:50%;background:var(--white);display:flex;align-items:center;justify-content:center}
.touch hr{border:0;border-top:1px solid #2b4674;width:185px;margin:22px 0 16px}
.socials{display:flex;gap:10px}
.socials span{width:30px;height:30px;border-radius:50%;border:1px solid #3b5a8a;display:flex;align-items:center;justify-content:center}
.socials span::after{content:"";width:7px;height:7px;border-radius:50%;background:var(--white)}
.foot-bar{position:absolute;left:0;bottom:0;width:1200px;height:66px;border-top:1px solid #1a3968;display:flex;align-items:center;justify-content:center;font-family:'Oswald',sans-serif;font-size:14px;text-transform:uppercase}
.legal{position:absolute;right:104px;bottom:24px;font-size:10px;color:#dbe6f5}
.chat-fab{position:absolute;left:1131px;top:4376px;width:48px;height:48px;border-radius:50%;background:#25b35a;display:flex;align-items:center;justify-content:center}
.top-fab{position:absolute;left:1136px;top:4468px;width:38px;height:38px;border-radius:50%;background:var(--gold);display:flex;align-items:center;justify-content:center;color:var(--white);font-size:14px}
</style>
</head>
<body>

<header class="site-header">
  <div class="brand"><span class="brand-dot"></span>Blue Keel Voyages</div>
  <nav class="main-nav">
    <span class="active">Home</span><span>Guna Yala</span><span>Fleet</span><span>About</span><span>Pricing</span><span>Itineraries</span><span>Activities</span><span>Blog</span><span>FAQs</span><span>Contact</span>
  </nav>
  <span class="lang">ENG ▾</span>
  <span class="btn">Book Now</span>
</header>

<section class="hero">
  <div class="photo hero-photo" role="img" aria-label="Sailing catamaran anchored off a green tropical island in turquoise water"></div>
  <svg class="abs" style="left:0;top:690px" width="1200" height="240" viewBox="0 0 1200 240" preserveAspectRatio="none">
    <path d="M0 200 C160 80 330 60 520 90 C720 120 900 150 1200 0 L1200 240 L0 240Z" fill="#7fd3ec"/>
    <path d="M0 240 C150 110 330 90 520 115 C720 140 930 175 1200 70 L1200 240Z" fill="#ffffff"/>
  </svg>
  <h1 class="abs display hero-title">San Blas Islands: Panama Sailing Vacations.</h1>
  <p class="abs hero-sub">Ultimate beaches &amp; catamaran tours</p>
  <span class="btn">Charter Inquiry Form</span>
</section>

<section class="about">
  <div class="photo about-photo" role="img" aria-label="Catamaran moored beside a sandy palm beach, seen from above"></div>
  <div class="abs eyebrow about-eyebrow">About</div>
  <h2 class="abs display about-title">Who We Are</h2>
  <p class="abs about-text">We're sailors and travelers with a love for exploration. When we first arrived in San Blas, its unique beauty and culture left a lasting impression. What began as a stop along our journey soon became something more—we felt a strong connection to this place and a sincere respect for its people, traditions, and way of life.</p>
  <span class="btn">Read More</span>
</section>

<section class="tours">
  <h2 class="abs display tours-title">Discover Ultimate<br>Panama Sailing Tours</h2>
  <article class="tour-card tour-private">
    <div class="tour-icon"><svg width="40" height="40" viewBox="0 0 40 40" fill="none" stroke="#fff" stroke-width="2.5"><circle cx="20" cy="20" r="10"/><circle cx="20" cy="20" r="3"/><path d="M20 4v32M4 20h32M9 9l22 22M31 9L9 31"/></svg></div>
    <h3>Private Charters</h3>
    <p>Sail the beautiful islands and beaches of San Blas on a private all-inclusive catamaran. Enjoy a custom itinerary, friendly crew, and flexible options to fit any budget—perfect...</p>
  </article>
  <article class="tour-card tour-shared">
    <div class="tour-icon"><svg width="40" height="40" viewBox="0 0 40 40" fill="#fff"><rect x="12" y="9" width="16" height="10" rx="3"/><path d="M6 20h28l-4 10H10z"/><path d="M5 33c4 2 6-2 10 0s6 2 10 0 6-2 10 0" stroke="#fff" stroke-width="2" fill="none"/></svg></div>
    <h3>Shared Charters</h3>
    <p>Share the experience with others for a more affordable alternative to a private charter. Perfect for couples, solo travelers, and small groups—enjoy San Blas beaches, clear waters,</p>
  </article>
  <article class="tour-card tour-family">
    <div class="tour-icon"><svg width="40" height="40" viewBox="0 0 40 40" fill="#fff"><path d="M20 6l8 14H12z"/><path d="M8 23h24l-3 6H11z"/><path d="M5 33c4 2 6-2 10 0s6 2 10 0 6-2 10 0" stroke="#fff" stroke-width="2" fill="none"/></svg></div>
    <h3>Family Friendly Boat Trips</h3>
    <p>San Blas is perfect for kids, with calm waters, safe snorkeling, and fun island-hopping. Families love the mix of adventure and culture—an ideal way to explore Panama together.</p>
  </article>
  <span class="btn">Request a Quote</span>
</section>

<section class="fleet">
  <svg class="abs fleet-bg" viewBox="0 0 1200 730" preserveAspectRatio="none">
    <defs><linearGradient id="fleetGrad" x1="0" y1="0" x2="0" y2="1"><stop offset="0" stop-color="#4cc1e0"/><stop offset="1" stop-color="#1596c4"/></linearGradient></defs>
    <path d="M0 150 C150 160 250 70 400 70 C600 70 700 180 900 170 C1050 160 1150 100 1200 0 L1200 690 C1000 710 600 700 300 690 C150 685 50 660 0 680Z" fill="url(#fleetGrad)"/>
    <path d="M0 150 C90 162 170 120 250 95 C150 160 60 185 0 175Z" fill="#ffffff" opacity=".6"/>
    <path d="M940 200 C1010 130 1120 150 1130 230 C1140 300 1060 330 1000 300 C950 280 910 250 940 200Z" fill="#f2a743" opacity=".85"/>
    <path d="M40 640 C80 600 150 610 160 660 C170 710 100 730 70 710 C40 690 20 670 40 640Z" fill="#f7ca91" opacity=".7"/>
  </svg>
  <h2 class="abs display fleet-title">Featured Catamarans</h2>
  <p class="abs fleet-sub">Catamaran rental San Blas: explore our Panama sailing fleet</p>

  <article class="boat-card" style="left:130px">
    <div class="boat-photo" role="img" aria-label="Aerial view of a white catamaran in deep blue water" style="background:linear-gradient(135deg,#1f5d80,#2a7da6)"></div>
    <div class="boat-body">
      <span class="tag">Catamaran</span>
      <h3>Marea 42</h3>
      <p class="desc">Service that exceeds all expectations!</p>
      <div class="specs">
        <span class="spec"><svg viewBox="0 0 14 14" fill="none" stroke="#0a2a5c" stroke-width="1.4"><path d="M2 12V2h10v10z"/></svg>55<br>SQFT</span>
        <span class="spec"><svg viewBox="0 0 14 14" fill="none" stroke="#0a2a5c" stroke-width="1.4"><path d="M2 11h10M3 11V6h8v5M5 6V3h4v3"/></svg>4<br>Cabin</span>
        <span class="spec"><svg viewBox="0 0 14 14" fill="none" stroke="#0a2a5c" stroke-width="1.4"><circle cx="7" cy="5" r="2.5"/><path d="M2 13c0-3 2-4.5 5-4.5s5 1.5 5 4.5"/></svg>8<br>Guest</span>
      </div>
      <span class="btn">Info &amp; Price</span>
    </div>
  </article>

  <article class="boat-card" style="left:450px">
    <div class="boat-photo" role="img" aria-label="Catamaran anchored in clear turquoise shallows" style="background:linear-gradient(135deg,#3aa6a6,#1f7f90)"></div>
    <div class="boat-body">
      <span class="tag">Catamaran</span>
      <h3>Coral 55F</h3>
      <p class="desc">Luxury and elegance on water!</p>
      <div class="specs">
        <span class="spec"><svg viewBox="0 0 14 14" fill="none" stroke="#0a2a5c" stroke-width="1.4"><path d="M2 12V2h10v10z"/></svg>39.5<br>SQFT</span>
        <span class="spec"><svg viewBox="0 0 14 14" fill="none" stroke="#0a2a5c" stroke-width="1.4"><path d="M2 11h10M3 11V6h8v5M5 6V3h4v3"/></svg>3<br>Cabin</span>
        <span class="spec"><svg viewBox="0 0 14 14" fill="none" stroke="#0a2a5c" stroke-width="1.4"><circle cx="7" cy="5" r="2.5"/><path d="M2 13c0-3 2-4.5 5-4.5s5 1.5 5 4.5"/></svg>6<br>Guest</span>
      </div>
      <span class="btn">Info &amp; Price</span>
    </div>
  </article>

  <article class="boat-card" style="left:768px">
    <div class="boat-photo" role="img" aria-label="Catamaran with teak deck sailing on open sea" style="background:linear-gradient(135deg,#26709a,#3b8fb8)"></div>
    <div class="boat-body">
      <span class="tag">Catamaran</span>
      <h3>Coral 55S</h3>
      <p class="desc">Safest family fun at sea!</p>
      <div class="specs">
        <span class="spec"><svg viewBox="0 0 14 14" fill="none" stroke="#0a2a5c" stroke-width="1.4"><path d="M2 12V2h10v10z"/></svg>47<br>SQFT</span>
        <span class="spec"><svg viewBox="0 0 14 14" fill="none" stroke="#0a2a5c" stroke-width="1.4"><path d="M2 11h10M3 11V6h8v5M5 6V3h4v3"/></svg>6<br>Cabin</span>
        <span class="spec"><svg viewBox="0 0 14 14" fill="none" stroke="#0a2a5c" stroke-width="1.4"><circle cx="7" cy="5" r="2.5"/><path d="M2 13c0-3 2-4.5 5-4.5s5 1.5 5 4.5"/></svg>12<br>Guest</span>
      </div>
      <span class="btn">Info &amp; Price</span>
    </div>
  </article>
</section>

<section class="testimonial">
  <div class="abs quote-mark">“</div>
  <div class="abs eyebrow testi-eyebrow">Testimonial</div>
  <h2 class="abs display testi-title">What They Say</h2>
  <p class="abs testi-text">Wow. We absolutely loved loved loved our time sailing through the San Blas islands. The food was absolutely amazing (highlights of lobster and octopus!) and enjoyed the daily cocktails after a day of relaxing while sailing through, snorkelling with captain Mateo and paddle boarding in paradise. The company were super helpful in organising the trip and our transport to get there from Panama City with excellent communication via ChatLine. The bedrooms and bathrooms are functional enough - we spent all our time outside anyway. Would not hesitate to recommend and I hope to go back one day!</p>
  <span class="arrow arrow-prev">‹</span>
  <span class="arrow arrow-next">›</span>
  <div class="photo testi-photo" role="img" aria-label="Happy guests swimming in the sea beside their catamaran"></div>
</section>

<section class="inquiry">
  <div class="photo inquiry-photo" role="img" aria-label="Catamaran at anchor in a calm turquoise bay below green hills"></div>
  <h2 class="abs display inquiry-title">Charter Inquiry Form</h2>
  <div class="form">
    <div class="row"><span class="field">Name</span><span class="field">Email</span><span class="field">ChatLine Number</span></div>
    <div class="radio-row"><span>Private Charter</span><span>Shared Charter</span></div>
    <div class="row"><span class="field">Number of Passengers</span><span class="field">Number of Days</span><span class="field">Date</span></div>
    <p class="label">What type of experience are you looking for? (Check all that apply)</p>
    <div class="row"><span class="field">Relaxing and disconnected</span></div>
    <div class="area"></div>
  </div>
  <span class="btn">Sent Message</span>
</section>

<footer class="site-footer">
  <div class="abs foot-mark">Blue Keel<br>Voyages</div>
  <p class="abs foot-about">Discover unforgettable catamaran and sailboat adventures in Guna Yala (San Blas), Panama. Blue Keel Voyages LLC offers all-inclusive island-hopping, snorkeling, and immersive cultural experiences—trusted by travelers worldwide.</p>
  <div class="abs explore">
    <h4 class="foot-h">Explore</h4>
    <ul><li>Home</li><li>Fleet</li><li>About Us</li><li>Contact</li><li>Pricing</li><li>Guna Yala</li><li>Itineraries</li><li>Activities</li><li>BOOK NOW</li><li>Blog</li></ul>
  </div>
  <div class="abs touch">
    <h4 class="foot-h">Get In Touch</h4>
    <div class="contact-item"><i><svg width="14" height="14" viewBox="0 0 14 14" fill="#0a2a5c"><path d="M3 1l2 3-1 1.5c.8 1.7 2 2.8 3.5 3.5L9 8l3 2-1 2.5C6 12.5 1.5 8 1.5 3z"/></svg></i><span>ChatLine:<br>+50760004821</span></div>
    <div class="contact-item"><i><svg width="14" height="14" viewBox="0 0 14 14" fill="none" stroke="#0a2a5c" stroke-width="1.4"><rect x="1.5" y="3" width="11" height="8" rx="1"/><path d="M1.5 3.5L7 8l5.5-4.5"/></svg></i><span>Email:<br>hello@bluekeelvoyages.net</span></div>
    <hr>
    <div class="socials"><span></span><span></span><span></span></div>
  </div>
  <div class="foot-bar">Copyright 2025 © Blue Keel Voyages, All rights reserved</div>
  <span class="legal">Privacy Policy &nbsp;|&nbsp; Terms &amp; Conditions</span>
</footer>
<span class="chat-fab"><svg width="22" height="22" viewBox="0 0 22 22" fill="#fff"><path d="M11 2a9 9 0 00-7.8 13.5L2 20l4.6-1.2A9 9 0 1011 2z"/></svg></span>
<span class="top-fab">˄</span>

</body>
</html>
```